The Orvane Codex Book Cover

"The Orvane Codex" is a book I wrote with the slogan "Unlock Performance, Spark Engagement: Master the Art of Building Winning Cultures in Today's Hybrid World". The book is designed around a methodology that's mine and that I attached. I would love to see the graphic of the methodology integrated in the design in a very subtle way. Use colors from the model but the book cover should be catchy, modern and engaging to the eye.
Overall the book is about three key elements towards success:
- (Self) Directions (purpose)
- Human experience (people and psychological safety)
- Maximize engagement
The methodology is a FLOW so flow is something that could be incorporated as well in the concept.
Low design quality
Managers and Teams

```html
<!DOCTYPE html>
<html lang="en">
<head>
<meta charset="UTF-8">
<title>The Orvane Codex – Book Cover</title>
<link rel="stylesheet" href="https://fonts.googleapis.com/css2?family=Bebas+Neue&family=Cinzel:wght@400&family=Montserrat:wght@500&display=swap">
<style>
  :root {
    --stage: #3b3b3d;
    --paper: #ffffff;
    --title-grey: #4d4e52;
    --accent-blue: #29a8e0;
    --band-blue: #1f8fd0;
    --ink-navy: #1f2537;
    --rule-grey: #c4c4c4;
    --author-grey: #58595b;
  }
  * { margin: 0; padding: 0; box-sizing: border-box; }
  html, body {
    width: 1200px; height: 1200px; overflow: hidden;
    background: var(--stage);
  }
  .cover {
    position: absolute; left: 220px; top: 31px;
    width: 759px; height: 1137px;
    background: var(--paper);
    overflow: hidden;
  }
  .title {
    font-family: "Bebas Neue", "Oswald", sans-serif;
    font-weight: 400;
    color: var(--title-grey);
  }
  .title-line {
    position: absolute; left: 0; right: 0;
    text-align: center; line-height: 1;
    letter-spacing: 2px; white-space: nowrap;
  }
  .title-line--first { top: 28px; font-size: 153px; }
  .title-line--second { top: 159px; font-size: 173px; letter-spacing: 4px; }
  .title .highlight { color: var(--accent-blue); }
  .band {
    position: absolute; left: 0; right: 0; height: 6px;
    background: linear-gradient(90deg, var(--band-blue), var(--accent-blue));
  }
  .band--top { top: 336px; }
  .band--bottom { top: 857px; }
  .hero {
    position: absolute; left: 0; right: 0; top: 342px; height: 515px;
    background:
      radial-gradient(ellipse at 25% 35%, rgba(190,200,90,0.55), transparent 45%),
      radial-gradient(ellipse at 55% 40%, rgba(150,120,200,0.5), transparent 45%),
      radial-gradient(ellipse at 80% 45%, rgba(110,180,210,0.5), transparent 40%),
      radial-gradient(ellipse at 88% 70%, rgba(220,150,80,0.4), transparent 35%),
      linear-gradient(180deg, #5a5b5e 0%, #4a4b4e 75%, #8a8a8a 82%, #b5b5b5 100%);
  }
  .rule {
    position: absolute; left: 92px; width: 575px; height: 1px;
    background: var(--rule-grey);
  }
  .rule--top { top: 887px; }
  .rule--bottom { top: 995px; }
  .tagline {
    position: absolute; left: 0; right: 0; top: 897px;
    text-align: center;
    font-family: "Bebas Neue", "Oswald", sans-serif;
    font-size: 35px; line-height: 1.1; letter-spacing: 1.4px;
    color: var(--accent-blue);
  }
  .subtitle {
    position: absolute; left: 0; right: 0; top: 932px;
    text-align: center;
    font-family: "Montserrat", sans-serif; font-weight: 500;
    font-size: 22px; line-height: 30px;
    color: var(--ink-navy);
  }
  .author {
    position: absolute; left: 0; right: 0; top: 1038px;
    text-align: center;
    font-family: "Cinzel", serif;
    font-size: 58px; letter-spacing: 10px;
    color: var(--author-grey);
  }
</style>
</head>
<body>
  <div class="cover">
    <h1 class="title">
      <span class="title-line title-line--first">THE <span class="highlight">ORVANE</span></span>
      <span class="title-line title-line--second">CODEX</span>
    </h1>
    <div class="band band--top"></div>
    <div class="hero" role="img" aria-label="Photo of five business people seen from behind, facing a grey wall covered in colourful chalk diagrams, arrows and sketches"></div>
    <div class="band band--bottom"></div>
    <div class="rule rule--top"></div>
    <p class="tagline">UNLOCK PERFORMANCE, SPARK ENGAGEMENT</p>
    <p class="subtitle">MASTER THE ART OF BUILDING<br>WINNING CULTURES IN TODAY’S HYBRID WORLD</p>
    <div class="rule rule--bottom"></div>
    <p class="author">JORIS ALTENA</p>
  </div>
</body>
</html>
```